Corporate website design needed

We need a Contemporary Industrial/Tech/Logistics Website design to match our logistic client's business. Our client consults and build logistics solutions that they manage but they are not a typical 3PL (3rd party logistics company) which is primarily engaged in moving boxes.
PSD file only for now, home and default templates.
COMPANY CHARACTER
DESIGN LOOK AND FEEL
• The design should also be modern and visually well organized — employing a combination of visual devices and info graphics. Keep it light and not too heavy but strong/ professional. And unique.
• The design should go beyond the typical industrial pick and pack 3PL representing [Logistics Company] as a High Tech/IT logistics company.
Some examples although these are not right for this client because they have much more content and present themselves more as a 3pl.
http://www.vobrelink-hub.example/ (More right then wrong - Like this but simplified)
http://www.durmaxfreight.example (Ugly)
http://www.tpwallerton.example (More right then wrong but different focus)
http://www.pelhamrye.example/ Too 3PL trucking… We want a bit ore high level approach
The difference, the design should be a fusion in core concepts that culminate in a design which implies the following attributes. Tech (Big data / analytics / software), Consultancy (Solutions, SME, Leader), 3PL Industry vertical solutions.
NOTE: The visualization of “tech” is not “1” and “0”, but more “software and analytics” Perhaps more like www.navimetra.example.
• They need to be seen as a solutions provider in Logistics and as in Subject matter experts
TONE
The tone needs to exude professionalism, expertise, though leadership along with technical and executional excellence.
Experienced
Knowledgeable
Confident
Determined
Straightforward
WEBSITE OBJECTIVES
• Focus C-Suite executives and logistics managers’ attention on [Logistics Company]s commanding knowledge and expertise, and unique approach to supply chain solutions producing more RFP wins
• Create an easy to scan design which decreases the reliance on text through featured text, summaries, and smaller “chunked” size bits of information.
• Convey [Logistics Company] as high-tech 3PL solutions developer and services provider with a ‘high-touch’ consultative approach.
• Showcase [Logistics Company]’s value propositions. (See Slider Content)
• Showcase [Logistics Company]’s expertise in logistical analytics.
• Gain recognition as an industry leader in evolutionary new space (supply chain 2.0)
WEBSITE STRATEGY
• Reduce reliance on text (at least within initial entry points for each section)
• Typography: Watch text line lengths and readability, bolder fonts. NO SERIFS
• Generally, create a click-through format so that users who want more details can find it, and those who don’t can get a snapshot without clicking through.
• Increase visual content through info graphics and some dynamic content, photography
• Better utilize the space on each page (e.g., add visual interest, photography and iconography where appropriate to break up copy blocks and maintain readable line lengths).
COLOR SCHEME
• Create a more engaging color scheme (the logo will remain the same under all circumstances).
• Red / grayscale may work…. Not too dark or heavy. Not too much red. Ex. quiltora.example
• Also try blues and greys. They seem to like that. Open to suggestions but don’t get to crazy. Red is in their logo but too much may be a problem.
PHOTOGRAPHY
Yes. And I will upload some.
If you pick photography please be sure to note Which stock house used and the image number!
CONTENT
The content will be presented in a more hierarchical format — with lead-ins, paragraph and section headers and navigational cues to expand lengthier content allowing the visitor to more easily scan the website. No case studies, No Social media, News while on the home page should not be over emphasized. They don't post a lot so it gets dated quickly ...
I will be uploading a wire frame and other elements.
NOTE: I uploaded my EXAMPLE mock up which is close but not close enough.
I am not a great designer. So I am looking for an alternative that exceed my design ability! These examples show the basic layout but I really want some varied alternatives.
The colors are inconsistent and type not quite right. The grey bar at top is not right and should probably go away.
Please pull the basic elements in the example together into a great design.
If you have questions please contact me.
i will upload some photography tomorrow that may be of use.
Thanks!
Updates
Hi All,
We are still evaluating the submitted designs. Sorry for the delay.
Target Market(s)
This website is primarily a validation website. Few new customers will search and find them as such...
The site should be Focused on C-Suite executives and logistics managers’ attention on [Logistics Company]s commanding knowledge and expertise, and unique approach to supply chain solutions producing more RFP wins
Industry/Entity Type
Business
Font styles to use
Requirements
Must have
- Slide show, Clearly explain who they are and what they do.
Create an easy to scan design which decreases the reliance on text through featured text, summaries, and smaller “chunked” size bits of information.
Convey [Logistics Company] as high-tech 3PL solutions developer and services
provider with a ‘high-touch’ consultative approach.
Should not have
- No Ads space
No Social media
Not too cluttered. Keep it clean.

```html
<!DOCTYPE html>
<html lang="en">
<head>
<meta charset="utf-8">
<title>Norvane Logistics</title>
<link href="https://fonts.googleapis.com/css2?family=Open+Sans:wght@400;600;700&display=swap" rel="stylesheet">
<style>
:root{
  --blue:#1b4f86;
  --blue-dark:#14395f;
  --nav-active:#1f63ad;
  --nav-bg:#3b3b3b;
  --red:#d0202b;
  --text:#444;
  --muted:#7a7a7a;
  --grey-bg:#f2f2f2;
  --line:#dedede;
  --footer:#0d4a82;
  --footer-bar:#0a2d52;
  --white:#fff;
}
*{margin:0;padding:0;box-sizing:border-box}
html,body{width:1200px;height:2799px;overflow:hidden}
body{font-family:"Open Sans",Arial,sans-serif;color:var(--text);background:var(--white);position:relative}
.abs{position:absolute}
p{font-size:12.5px;line-height:19px}
.btn{position:absolute;display:block;color:var(--white);font-size:13px;font-weight:600;text-align:center;border-radius:3px;
  background:linear-gradient(#2f5d89,#163a60);box-shadow:0 2px 3px rgba(0,0,0,.25);text-decoration:none}
.heading{color:var(--blue);font-weight:600}

/* header */
.brand{left:112px;top:36px;display:flex;align-items:center;gap:10px}
.brand-dot{width:40px;height:40px;border-radius:50%;border:3px solid var(--red)}
.brand-name{font-size:19px;font-weight:600;letter-spacing:3px;color:#333;text-transform:uppercase}
.phone{left:864px;top:34px;display:flex;align-items:center;gap:6px;font-size:25px;color:#333}
.phone .label{color:var(--red)}

/* nav */
.nav{left:0;top:110px;width:1200px;height:47px;background:var(--nav-bg);border-bottom:3px solid var(--nav-active)}
.nav ul{list-style:none}
.nav li{position:absolute;top:0;height:44px;line-height:44px;font-size:14px;color:#eee}
.nav li.active{background:var(--nav-active);left:110px;width:112px;text-align:center;font-weight:600}
.search{left:817px;top:6px;width:273px;height:31px;background:var(--white);border-radius:2px;font-size:12px;color:#aaa;line-height:31px;padding-left:10px}
.search svg{position:absolute;right:8px;top:7px}

/* hero */
.hero{left:0;top:157px;width:1200px;height:502px;
  background:radial-gradient(ellipse at 55% 70%,#f7d38a 0%,#e39a3e 18%,#8a5a33 45%,#3f3a35 75%,#2a2826 100%)}
.hero-panel{left:112px;top:284px;width:353px;height:233px;background:rgba(255,255,255,.85);border-left:3px solid var(--blue);padding:10px 12px}
.hero-panel h1{font-size:32px;font-weight:600;color:var(--blue);line-height:40px;letter-spacing:-.6px;white-space:nowrap}
.hero-panel h2{font-size:15px;font-weight:600;color:#222;margin:0 0 14px}
.hero-panel p{font-size:12px;line-height:17px;color:#333}
.hero-panel .btn{left:15px;top:173px;width:114px;height:37px;line-height:37px}

/* features */
.feature{position:absolute;top:715px;width:321px;height:162px}
.feature.card{background:var(--white);box-shadow:0 8px 10px -6px rgba(0,0,0,.25);border:1px solid #eee}
.feature .icon{position:absolute;left:14px;top:15px;width:70px;height:70px;border-radius:50%;background:#f4f4f4;border:3px solid #e3e3e3;display:flex;align-items:center;justify-content:center}
.feature h3{position:absolute;left:99px;top:32px;font-size:15px;font-weight:600;color:#222;line-height:21px}
.feature p{position:absolute;left:99px;top:80px;width:210px;font-size:12px;line-height:19px;color:#666}

/* grey band */
.band{left:0;top:948px;width:1200px;height:1146px;background:var(--grey-bg)}
.divider{left:110px;width:980px;height:1px;background:var(--line)}
.media{box-shadow:0 2px 4px rgba(0,0,0,.3)}
.section-title{font-size:30px}
.subtitle{font-size:14px;font-weight:600;color:var(--muted)}

.video{left:110px;top:1008px;width:476px;height:272px;background:linear-gradient(135deg,#e6e2dc,#b9a995 50%,#4b4d55)}
.video-bar{position:absolute;left:0;bottom:0;width:100%;height:26px;background:#1e1e1e}
.play{position:absolute;left:214px;top:100px}

.plans{left:625px;top:1372px;width:465px;height:287px;background:linear-gradient(160deg,#e9f0f6,#c7d6e3 55%,#e7d48a)}
.slider{left:114px;top:1758px;width:464px;height:278px;background:linear-gradient(#6fa0d0,#9cbfe0 45%,#3b4d5a 70%,#6aa6c4)}
.slider .side{position:absolute;top:0;width:34px;height:100%;background:rgba(20,20,20,.75)}

/* news / about */
.news-item{position:absolute;left:110px;width:460px}
.thumb{position:absolute;left:0;top:0;width:82px;height:70px;background:linear-gradient(#dfe4ea,#7d8590)}
.news-item p{position:absolute;left:90px;top:-2px;width:370px;font-size:12px;line-height:18px}
.date{position:absolute;left:90px;top:38px;font-size:12px;color:#333}
.more{position:absolute;left:90px;top:66px;font-size:12px;color:var(--blue)}

/* footer */
.footer{left:0;top:2482px;width:1200px;height:280px;background:linear-gradient(#115390,#0b3f73)}
.footer h4{position:absolute;top:63px;font-size:19px;font-weight:600;color:var(--white);text-transform:uppercase}
.footer ul{position:absolute;top:96px;list-style:none}
.footer li{font-size:13px;line-height:20px;color:#e4ecf5}
.footer .brand-name{color:var(--white);font-size:15px}
.footer .brand-dot{width:32px;height:32px;border-color:var(--white);border-width:2px}
.foot-bar{left:0;top:2762px;width:1200px;height:37px;background:var(--footer-bar);color:#cdd7e2;font-size:12px;line-height:37px}
.foot-bar .links{position:absolute;right:110px;top:0}
.foot-bar .links span{margin:0 8px}
.foot-bar .links .current{color:#4aa3ff}
</style>
</head>
<body>

<header>
  <div class="abs brand"><span class="brand-dot"></span><span class="brand-name">Norvane</span></div>
  <div class="abs phone">
    <svg width="22" height="24" viewBox="0 0 24 24"><path d="M6 2l4 4-2 3c1 3 4 6 7 7l3-2 4 4-3 4C10 22 2 14 2 5z" fill="#d0202b"/></svg>
    <span class="label">Call:</span><span>866 555 0142</span>
  </div>
</header>

<nav class="abs nav">
  <ul>
    <li class="active">HOME</li>
    <li style="left:252px">Careers</li>
    <li style="left:345px">Solutions</li>
    <li style="left:446px">Our Process</li>
    <li style="left:567px">Industries</li>
    <li style="left:674px">Contact Us</li>
  </ul>
  <div class="abs search">Search
    <svg width="16" height="16" viewBox="0 0 16 16"><circle cx="6.5" cy="6.5" r="5" fill="none" stroke="#bbb" stroke-width="1.6"/><path d="M10 10l5 5" stroke="#bbb" stroke-width="1.8"/></svg>
  </div>
</nav>

<section>
  <div class="abs hero" role="img" aria-label="Photo of a worker cutting metal with an angle grinder and flying sparks"></div>
  <div class="abs hero-panel">
    <h1>A new way to think</h1>
    <h2>About Supply Chain Transformation</h2>
    <p>Lorem ipsum dolor sit amet consectetur adipisicing elit eiusmod tempor incididunt ut labore et dolore magna aliqua. Ut ad minim veniam quis nostrud exercitation ullam</p>
    <a class="btn">Read More</a>
  </div>
</section>

<section>
  <div class="feature card" style="left:112px">
    <div class="icon"><svg width="38" height="34" viewBox="0 0 38 34"><path d="M2 32V14l9 6v-6l9 6v-6l9 6V4h6v28z" fill="#1b4f86"/></svg></div>
    <h3>Material managment &amp;<br>Factory Support</h3>
    <p>Ut enim ad minim veniam nostrud exercitation ullamco laboris nisi ut aliquip ex ea commodo.</p>
  </div>
  <div class="feature" style="left:465px">
    <div class="icon"><svg width="36" height="36" viewBox="0 0 36 36" fill="none" stroke="#333" stroke-width="2"><circle cx="18" cy="18" r="15"/><ellipse cx="18" cy="18" rx="7" ry="15"/><path d="M3 18h30M6 10h24M6 26h24"/></svg></div>
    <h3>Retail and<br>e-commerc Distribution</h3>
    <p>Ut enim ad minim veniam nostrud exercitation ullamco laboris nisi ut aliquip ex ea commodo.</p>
  </div>
  <div class="feature" style="left:797px">
    <div class="icon"><svg width="30" height="36" viewBox="0 0 30 36"><rect x="4" y="2" width="22" height="26" rx="3" fill="#333"/><rect x="8" y="6" width="14" height="8" fill="#eee"/><rect x="2" y="28" width="6" height="6" fill="#333"/><rect x="22" y="28" width="6" height="6" fill="#333"/></svg></div>
    <h3>Supply chain<br>transformation Services</h3>
    <p>Ut enim ad minim veniam nostrud exercitation ullamco laboris nisi ut aliquip ex ea commodo.</p>
  </div>
</section>

<section>
  <div class="abs band"></div>

  <div class="abs video media" role="img" aria-label="Video still of a business team meeting around a table">
    <svg class="play" width="48" height="48" viewBox="0 0 48 48"><circle cx="24" cy="24" r="23" fill="rgba(0,0,0,.6)"/><path d="M19 14l15 10-15 10z" fill="#fff"/></svg>
    <div class="video-bar">
      <svg width="476" height="26" viewBox="0 0 476 26"><rect x="0" y="0" width="476" height="4" fill="#555"/><rect x="0" y="0" width="200" height="4" fill="#d0202b"/><path d="M10 9h3v10h-3zM16 9h3v10h-3z" fill="#ccc"/><path d="M32 11h4l5-4v14l-5-4h-4z" fill="#ccc"/><rect x="48" y="13" width="40" height="3" fill="#d0202b"/><rect x="450" y="9" width="12" height="10" fill="none" stroke="#ccc" stroke-width="1.5"/></svg>
    </div>
  </div>
  <h2 class="abs heading section-title" style="left:629px;top:1001px">The Norvane Difference</h2>
  <div class="abs subtitle" style="left:629px;top:1040px">Corporat profile</div>
  <div class="abs" style="left:629px;top:1075px;width:461px">
    <p>Lorem ipsum dolor sit amet consectetur adipisicing elit eiusmod tempor incididunt ut labore et dolore magna aliqua. Ut ad minim veniam quis nostrud exercitation ullam irure in reprehenderit in voluptate velit esse cillum dolore eu fugiat nulla pariatur.</p>
    <p style="margin-top:12px">Excepteur sint occaecat cupidatat non proident, sunt in culpa qui officia deserunt mollit anim id est laborum.</p>
  </div>
  <a class="btn" style="left:629px;top:1217px;width:114px;height:39px;line-height:39px">Read More</a>

  <div class="abs divider" style="top:1325px"></div>

  <h2 class="abs heading section-title" style="left:110px;top:1361px">The Norvane Difference</h2>
  <div class="abs" style="left:114px;top:1425px;width:400px">
    <p>We commit our own capital and resources to align with our client' goals</p>
    <p style="margin-top:14px">Unlike consultants, we implement and operate the solutions we design</p>
    <p style="margin-top:14px">we guarantee business performance for our clientsby investing in and executing the solution we design.</p>
  </div>
  <a class="btn" style="left:114px;top:1616px;width:112px;height:38px;line-height:38px">Read More</a>
  <div class="abs plans media" role="img" aria-label="Photo of blueprints with glasses, a tape measure and a hard hat, people in the background"></div>

  <div class="abs divider" style="top:1706px"></div>

  <div class="abs slider media" role="img" aria-label="Photo of a modern house with a pool at dusk">
    <div class="side" style="left:0"><svg width="34" height="278" viewBox="0 0 34 278"><path d="M22 124l-10 15 10 15" fill="none" stroke="#fff" stroke-width="3"/></svg></div>
    <div class="side" style="right:0"><svg width="34" height="278" viewBox="0 0 34 278"><path d="M12 124l10 15-10 15" fill="none" stroke="#fff" stroke-width="3"/></svg></div>
  </div>
  <h2 class="abs heading section-title" style="left:648px;top:1749px">Featured Industry</h2>
  <div class="abs" style="left:651px;top:1798px;width:440px">
    <p>Lorem ipsum dolor sit amet consectetur adipisicing elit eiusmod tempor incididunt ut labore et dolore magna aliqua. Ut ad minim veniam quis nostrud exercitation ullam irure in reprehenderit in voluptate velit esse cillum dolore eu fugiat nulla pariatur.</p>
    <p style="margin-top:12px">Excepteur sint occaecat cupidatat non proident, sunt in culpa qui officia deserunt mollit anim id est laborum.</p>
  </div>
  <a class="btn" style="left:651px;top:1967px;width:112px;height:39px;line-height:39px">Read More</a>
</section>

<section>
  <h2 class="abs heading section-title" style="left:110px;top:2130px">Recent News</h2>
  <div class="news-item" style="top:2183px">
    <div class="thumb" role="img" aria-label="Portrait photo of a businessman"></div>
    <p>Lorem ipsum dolor sit amet, consectetur adipisicing elit, sed eiusmod tempor incididunt ut labore et dolore magna aliqua.</p>
    <span class="date">21 Jan</span><span class="more">Read More...</span>
  </div>
  <div class="news-item" style="top:2286px">
    <div class="thumb" role="img" aria-label="Portrait photo of a businessman"></div>
    <p>Lorem ipsum dolor sit amet, consectetur adipisicing elit, sed eiusmod tempor incididunt ut labore et dolore magna aliqua.</p>
    <span class="date">21 Jan</span><span class="more">Read More...</span>
  </div>
  <a class="btn" style="left:110px;top:2396px;width:174px;height:38px;line-height:38px">More Norvane News</a>

  <h2 class="abs heading section-title" style="left:612px;top:2130px">ABOUT US</h2>
  <div class="abs" role="img" aria-label="Photo of people working at computers in an office" style="left:610px;top:2185px;width:112px;height:101px;background:linear-gradient(#e8eef3,#9fb3c4)"></div>
  <div class="abs" style="left:731px;top:2179px;width:360px">
    <p style="font-size:12px;line-height:18px">Lorem ipsum dolor sit amet consectetur adipisicing elit eiusmod tempor incididunt ut labore et dolore magna aliqua. Ut ad minim veniam quis nostrud exercitation ullam irure in reprehenderit in voluptate velit esse cillum dolore eu fugiat nulla pariatur.</p>
    <p style="font-size:12px;line-height:18px;margin-top:10px">Excepteur sint occaecat cupidatat non proident, sunt in culpa qui officia deserunt mollit anim id est laborum.</p>
  </div>
  <a class="btn" style="left:731px;top:2346px;width:112px;height:39px;line-height:39px">Read More</a>
</section>

<footer>
  <div class="abs footer">
    <h4 style="left:112px">About Company</h4>
    <div class="abs brand" style="left:112px;top:100px;gap:8px"><span class="brand-dot"></span><span class="brand-name">Norvane</span></div>
    <p class="abs" style="left:112px;top:150px;width:196px;font-size:13px;line-height:19px;color:#e4ecf5">Lorem ipsum dolor sit amet consectetur adipisicing elit eiusmod tempor incididunt ut labore et dolore magna aliqua ad minim veniam quis nostrud exercitation ullam.</p>

    <h4 style="left:381px">Our Process</h4>
    <ul style="left:381px">
      <li>Concept of operations</li><li>Supplying the infrastructure</li><li>Analyzing the data</li><li>Managing complexity</li><li>Providing actionable strategies</li><li>Nvesting in our client's success</li><li>Driving business results</li>
    </ul>

    <h4 style="left:644px">Our Solutions</h4>
    <ul style="left:644px">
      <li>Business Analytics</li><li>Geographic Coverage</li><li>Project financing</li><li>Project implementation</li><li>Technology</li><li>Quality</li>
    </ul>

    <h4 style="left:885px">Industries We Serve</h4>
    <ul style="left:885px">
      <li>Aerospace</li><li>defense</li><li>Industrial</li><li>Manufacturing</li><li>Media and Entertainment</li><li>Medical</li><li>Retail</li><li>Telecom &amp; Electroincs</li>
    </ul>
  </div>
  <div class="abs foot-bar">
    <span style="position:absolute;left:112px">Copyright ©2014 Norvane. All Rights Reserved.</span>
    <div class="links"><span class="current">Home</span>|<span>Careers</span>|<span>Solutions</span>|<span>Our Process</span>|<span>Industries</span>|<span>Contact Us</span></div>
  </div>
</footer>

</body>
</html>
```